Web Design for Independent Pet Supply shop.

Larch Critter Depot is a locally owned and operated premium natural pet food store and supply company with 2 thriving retail stores in Bend, Oregon, and a home delivery service. The pet food offered is the best on the market and may be described as “holistic”. Also on offer is a vast selection of toys, training tools, treats, and other supplies, as well as dog washing services that range from "do-it yourself" to "spa." Current site: LarchCritterDepot.com. They need a new, updated and responsive site.
Likes:
Tovanels.com: Natural colors, not loud, pages in motion, simple & clean but very informative.
Dorvikmerin.com: Everything in simple big colorful blocks. The specials run across the top and in motion. This site looks very professional but simple. The information is available several different places.
Plenharvest.com: Again big blocks through out. Very Fun and inviting. Tons of information with videos and recipes and testimonials. Pleasant feel and colors as well.
Dislikes:
Furlix.com: Looks cheap, hate the colors, very busy and over whelming. Hate the old style header bar going across with options. Too many printed words instead of fun images.
Colors should be "natural" tones, warm and soothing. Deep dark blue and greys with earthy wood color.
Do Not Use: Blue violet, violet, red violet

```html
<!DOCTYPE html>
<html lang="en">
<head>
<meta charset="utf-8">
<title>Larch Critter Depot</title>
<link rel="stylesheet" href="https://fonts.googleapis.com/css2?family=Lato:wght@400;700&family=Questrial&display=swap">
<style>
:root{
  --navy:#1d2d6e;
  --wood:#b8884b;
  --wood-dark:#a87a3f;
  --grey-text:#5a5a5a;
  --light-grey:#f4f4f4;
  --line:#dcdcdc;
  --footer:#0e0e0e;
  --footer-line:#2c2c2c;
  --white:#ffffff;
}
*{margin:0;padding:0;box-sizing:border-box}
html,body{width:1200px;height:2317px;overflow:hidden;background:var(--white)}
body{position:relative;font-family:"Lato",sans-serif;color:var(--grey-text)}
.abs{position:absolute}

/* header */
.site-header{left:0;top:0;width:1200px;height:100px;background:var(--white)}
.brand{left:94px;top:30px;display:flex;align-items:center;gap:10px}
.brand-dot{width:34px;height:34px;border-radius:50%;background:var(--wood)}
.brand-name{font-family:"Lato",sans-serif;font-weight:700;font-size:26px;color:var(--wood);letter-spacing:.5px}
.main-nav{left:432px;top:50px;display:flex;font-family:"Questrial",sans-serif;font-size:13px;text-transform:uppercase;color:#777}
.main-nav span{position:relative;margin-right:31px}
.main-nav .active{color:var(--wood)}
.main-nav .active::after{content:"";position:absolute;left:0;right:0;bottom:-9px;height:1px;background:var(--wood)}

/* hero */
.hero{left:0;top:100px;width:1200px;height:398px;background:linear-gradient(90deg,#1184f2 0%,#4aa6f0 40%,#9ccaf0 70%,#c8dcf2 100%)}
.hero-photo{right:0;top:0;width:820px;height:398px;background:linear-gradient(200deg,rgba(225,60,40,.85) 0%,rgba(230,90,70,.55) 30%,rgba(220,190,170,.3) 60%,rgba(255,255,255,0) 80%)}
.hero-title{left:94px;top:232px;font-family:"Questrial",sans-serif;font-weight:400;font-size:40px;line-height:50px;color:var(--white);letter-spacing:.5px}
.hero-dots{left:96px;top:348px;display:flex;gap:5px}
.hero-dots i{width:9px;height:9px;border-radius:50%;background:var(--white)}
.hero-dots i.on{background:var(--wood)}

/* intro */
.intro{left:150px;top:516px;width:900px;text-align:center;font-size:19.5px;line-height:30px;color:var(--navy)}

/* service tiles */
.tiles{left:94px;top:603px;width:1011px;display:grid;grid-template-columns:repeat(3,307px);column-gap:45px;row-gap:24px}
.tile{position:relative;height:211px;overflow:hidden}
.tile-img{width:100%;height:100%}
.tile-label{position:absolute;left:0;bottom:0;width:100%;height:28px;background:var(--wood);color:var(--white);font-size:13px;font-weight:700;letter-spacing:.6px;text-transform:uppercase;text-align:center;line-height:28px}
.tile-label.navy{background:var(--navy)}
.haven{display:flex;flex-direction:column;align-items:center;justify-content:center;background:#f1f1f1;padding-bottom:28px}
.haven span{font-family:"Lato",sans-serif;font-weight:700;color:#8c9c2e;font-size:17px;text-align:center;line-height:24px}

/* news */
.news-title{left:94px;top:1360px;font-family:"Questrial",sans-serif;font-weight:400;font-size:28px;color:#222}
.news-title b{font-weight:400;color:var(--navy)}
.news-rule{left:94px;top:1406px;width:1011px;height:1px;background:var(--line)}
.news-rule::before{content:"";position:absolute;left:0;top:-1px;width:62px;height:2px;background:var(--navy)}
.news-arrows{left:1068px;top:1366px}
.news-item{width:492px;height:140px}
.date-box{position:absolute;left:0;top:0;width:60px;height:80px;background:var(--wood);color:var(--white);text-align:center;border-radius:3px}
.date-box .d{font-size:26px;font-weight:700;line-height:30px;padding-top:5px;display:block}
.date-box .m{font-size:12px;line-height:14px;display:block}
.news-body{position:absolute;left:80px;top:0;width:410px}
.news-body h3{font-size:14.5px;font-weight:700;color:#222;margin-bottom:9px}
.news-body p{font-size:12.5px;line-height:19px;color:#444}
.more-btn{display:inline-block;margin-top:10px;border:1px solid var(--wood);color:var(--wood);font-size:12px;padding:1px 10px;line-height:17px}
.news-sep{top:1569px;height:1px;width:492px;background:var(--line)}

/* about */
.about{left:0;top:1731px;width:1200px;height:271px;background:var(--light-grey)}
.about h2{position:absolute;left:0;top:34px;width:1200px;text-align:center;font-family:"Questrial",sans-serif;font-weight:400;font-size:28px;color:#222}
.about h2 b{font-weight:400;color:var(--navy)}
.about-rule{left:94px;top:81px;width:1011px;height:1px;background:var(--line)}
.about-rule::before{content:"";position:absolute;left:475px;top:-1px;width:62px;height:2px;background:var(--navy)}
.about p{position:absolute;left:94px;top:100px;width:1011px;text-align:center;font-size:18px;line-height:28.5px;color:var(--grey-text)}
.about .more-btn{position:absolute;left:559px;top:216px;margin:0;font-size:12.5px}

/* footer */
.site-footer{left:0;top:2002px;width:1200px;height:272px;background:var(--footer)}
.foot-head{font-family:"Questrial",sans-serif;font-size:18px;color:var(--white);text-transform:uppercase;letter-spacing:.5px;padding-bottom:10px;border-bottom:1px solid var(--wood)}
.quick-links{left:94px;top:32px;width:205px}
.link-grid{display:grid;grid-template-columns:100px 100px;column-gap:14px;margin-top:6px}
.link-grid span{display:block;font-size:14px;color:#ddd;line-height:33.5px;border-bottom:1px dotted #333}
.inquiry{left:398px;top:32px;width:208px;height:225px}
.field{position:absolute;left:0;width:208px;border:1px solid #bbb;height:31px;font-size:13px;font-style:italic;color:#ddd;padding:6px 4px}
.field.name{top:43px}
.field.email{top:83px}
.field.msg{top:125px;height:59px}
.submit{position:absolute;right:0;top:196px;background:var(--navy);color:var(--white);font-size:13px;font-weight:700;padding:4px 12px;line-height:17px;border-radius:2px}
.follow{left:708px;top:32px;width:152px}
.social{margin-top:12px;display:flex;align-items:center;gap:10px;font-size:12px;font-weight:700;color:var(--white);text-transform:uppercase;height:28px}
.social i{width:27px;height:27px;border-radius:50%}
.badge-circle{left:960px;top:80px;width:146px;height:146px;border-radius:50%;background:#4a4a4a}
.copyright{left:0;top:2274px;width:1200px;height:43px;background:var(--footer);border-top:1px solid var(--footer-line);text-align:center;line-height:42px;font-size:11.5px;font-weight:700;color:var(--white)}
</style>
</head>
<body>

<header class="abs site-header">
  <div class="abs brand"><span class="brand-dot"></span><span class="brand-name">Larch Critter Depot</span></div>
  <nav class="abs main-nav">
    <span class="active">Home</span><span>Events</span><span>Blog</span><span>Dog Wash</span><span>Products</span><span>Resources</span><span>Links</span><span>Contact</span>
  </nav>
</header>

<section class="abs hero">
  <div class="abs hero-photo" role="img" aria-label="Dog wearing sunglasses lounging under a red beach umbrella against a blue sky"></div>
  <h1 class="abs hero-title">Dedicated To A Better Diet<br>For A Healthier Pet</h1>
  <div class="abs hero-dots"><i class="on"></i><i></i><i></i><i></i></div>
</section>

<p class="abs intro">Lorem ipsum dolor sit amet, consectetur adipiscing elit mauris at porta libero, vitae commodo dui vestibulum sed eros eget magna aliquet iaculis in vitae lorem</p>

<section class="abs tiles">
  <div class="tile"><div class="tile-img" role="img" aria-label="Pink plush dog toy" style="background:linear-gradient(160deg,#e7e2df,#d44a9a 55%,#c8b8b8)"></div><div class="tile-label navy">Vast Selection of Toys</div></div>
  <div class="tile"><div class="tile-img" role="img" aria-label="Leashes, collars and training tools laid out on a table" style="background:linear-gradient(160deg,#3c4a66,#6b7a4a 50%,#c26a3a)"></div><div class="tile-label">Training Tools</div></div>
  <div class="tile"><div class="tile-img" role="img" aria-label="Bone shaped dog biscuits" style="background:linear-gradient(160deg,#e6c79a,#cfa06a 60%,#b98854)"></div><div class="tile-label">Treats</div></div>
  <div class="tile"><div class="tile-img" role="img" aria-label="Colourful pet bowls and toy balls" style="background:linear-gradient(160deg,#f0a060,#3a9ad8 55%,#e8d060)"></div><div class="tile-label">Other Supplies</div></div>
  <div class="tile"><div class="tile-img" role="img" aria-label="Golden retriever being washed" style="background:linear-gradient(160deg,#dfe6ec,#c08a4a 55%,#8f6230)"></div><div class="tile-label">Dog Washing</div></div>
  <div class="tile"><div class="tile-img" role="img" aria-label="Cat relaxing in white towels at a pet spa" style="background:linear-gradient(160deg,#f4f4f2,#e6e2dc 55%,#d89050)"></div><div class="tile-label">Spa for Pets</div></div>
  <div class="tile"><div class="tile-img" role="img" aria-label="Dog drinking from a red bowl on grass" style="background:linear-gradient(160deg,#6a8a3a,#5a5e66 50%,#4a7a2a)"></div><div class="tile-label">Hound Brew</div></div>
  <div class="tile"><div class="tile-img" role="img" aria-label="Bag of dog food beside scales of justice" style="background:linear-gradient(160deg,#1c3a6a,#3a5a8a 50%,#a8843a)"></div><div class="tile-label">Pawvena Lawsuit</div></div>
  <div class="tile haven"><span>Haven Community<br>Pet Food Bank</span><div class="tile-label">Haven Community Food Bank</div></div>
</section>

<h2 class="abs news-title">Recent <b>News &amp; Events</b></h2>
<svg class="abs news-arrows" width="37" height="22" viewBox="0 0 37 22" aria-hidden="true"><path d="M11 2 L3 11 L11 20" fill="none" stroke="#555" stroke-width="1.6"/><path d="M26 2 L34 11 L26 20" fill="none" stroke="#555" stroke-width="1.6"/></svg>
<div class="abs news-rule"></div>

<article class="abs news-item" style="left:94px;top:1430px">
  <div class="date-box"><span class="d">01</span><span class="m">Jan<br>2016</span></div>
  <div class="news-body"><h3>Lorem Ipsum Dolor  Consecte</h3><p>Sed ut perspiciatis unde omnis iste natus error sit voluptatem accusantium dolo remque laudantium, totam rem aperiam, eaque ipsa quae ab illo inventore veritatis et quasi architecto beatae</p><span class="more-btn">read more</span></div>
</article>
<article class="abs news-item" style="left:612px;top:1430px">
  <div class="date-box"><span class="d">01</span><span class="m">Jan<br>2016</span></div>
  <div class="news-body"><h3>Lorem Ipsum Dolor  Consecte</h3><p>Sed ut perspiciatis unde omnis iste natus error sit voluptatem accusantium dolo remque laudantium, totam rem aperiam, eaque ipsa quae ab illo inventore veritatis et quasi architecto beatae</p><span class="more-btn">read more</span></div>
</article>
<div class="abs news-sep" style="left:94px"></div>
<div class="abs news-sep" style="left:612px"></div>
<article class="abs news-item" style="left:94px;top:1592px">
  <div class="date-box"><span class="d">30</span><span class="m">Dec<br>2015</span></div>
  <div class="news-body"><h3>Lorem Ipsum Dolor  Consecte</h3><p>Duis autem vel eum iriure dolor in hendreri inmo vulputate velit esse molestie consequatn vel illum dolore eu feugiat nulla facilisis...</p><span class="more-btn">read more</span></div>
</article>
<article class="abs news-item" style="left:612px;top:1592px">
  <div class="date-box"><span class="d">30</span><span class="m">Dec<br>2015</span></div>
  <div class="news-body"><h3>Lorem Ipsum Dolor  Consecte</h3><p>Duis autem vel eum iriure dolor in hendreri inmo vulputate velit esse molestie consequatn vel illum dolore eu feugiat nulla facilisis...</p><span class="more-btn">read more</span></div>
</article>

<section class="abs about">
  <h2>About <b>Us</b></h2>
  <div class="abs about-rule"></div>
  <p>Lorem ipsum dolor sit amet, consectetur adipiscing elit. Mauris at porta libero, vitae commodo dui. Vestibulum sed eros eget magna aliquet iaculis in vitae lorem. Nunc sed eros quis lacus pharetra consequat non in erat.<br>Curabitur semper nisi dolor, at cursus sapien rutrum et</p>
  <span class="more-btn">Read More</span>
</section>

<footer class="abs site-footer">
  <div class="abs quick-links">
    <div class="foot-head">Quick Links</div>
    <div class="link-grid">
      <span>Home</span><span>Products</span>
      <span>Events</span><span>Resources</span>
      <span>Blog</span><span>Links</span>
      <span>About</span><span>Contact</span>
      <span>Dog Wash</span>
    </div>
  </div>
  <div class="abs inquiry">
    <div class="foot-head">Quick Inquiry</div>
    <div class="field name">Full Name</div>
    <div class="field email">Email</div>
    <div class="field msg">Message</div>
    <span class="submit">SUBMIT &#8250;</span>
  </div>
  <div class="abs follow">
    <div class="foot-head">Follow Us On</div>
    <div class="social"><i style="background:#3b5a94"></i>Friendloop</div>
    <div class="social"><i style="background:#2a9ad4"></i>Chirpline</div>
    <div class="social"><i style="background:#a0704a"></i>Pictello</div>
    <div class="social"><i style="background:#d0402e"></i>Searchly</div>
  </div>
  <div class="abs badge-circle"></div>
</footer>
<div class="abs copyright">Copyright © 2016 Larch Critter Depot . All Rights Reserved.</div>

</body>
</html>
```